BOLD & MINIMALIST DESIGN NEEDED

We want a very bold but minimalistic business card design that is impactful and utilizes both sides of the business card. Our current logo is included for your use.

We want bold fonts and good use of negative space. We don't want the logo to overpower the design.

Target Market(s)

Professionals who are building new commercial buildings.

Industry/Entity Type

Construction

Contact Information for Business Card

Name, Title, email, office phone, cell phone, website

Font styles to use
Serif
Sans Serif

Requirements
Must have
• Bold design!

```html
<!DOCTYPE html>
<html lang="en">
<head>
<meta charset="utf-8">
<title>Ridgeline Design + Build — Business Card</title>
<link rel="stylesheet" href="https://fonts.googleapis.com/css2?family=Archivo+Black&family=Poppins:wght@400;500;600&display=swap">
<style>
  :root {
    --stage: #1c1c1c;
    --card-black: #0a0a0a;
    --card-white: #ffffff;
    --brand-green: #7dc142;
    --ink: #111111;
    --ink-soft: #333333;
    --white: #ffffff;
  }
  * { margin: 0; padding: 0; box-sizing: border-box; }
  html, body { width: 1200px; height: 875px; overflow: hidden; }
  body {
    background: var(--stage);
    position: relative;
    font-family: "Poppins", sans-serif;
  }
  .card {
    position: absolute;
    width: 560px;
    height: 320px;
    border-radius: 22px;
    overflow: hidden;
    box-shadow: 0 24px 50px rgba(0,0,0,0.55);
  }

  /* Front side */
  .card-front { left: 70px; top: 80px; background: var(--card-black); }
  .front-curve { position: absolute; inset: 0; }
  .front-brand {
    position: absolute;
    left: 48px;
    top: 70px;
    display: flex;
    align-items: flex-start;
    gap: 18px;
  }
  .brand-square {
    width: 34px; height: 34px;
    background: var(--brand-green);
    margin-top: 10px;
  }
  .front-brand .brand-name {
    font-family: "Archivo Black", sans-serif;
    color: var(--white);
    font-size: 52px;
    line-height: 1;
    letter-spacing: 0.5px;
  }
  .front-brand .brand-name span {
    display: block;
    font-size: 19px;
    letter-spacing: 7px;
    margin-top: 10px;
  }

  /* Back side */
  .card-back { left: 570px; top: 470px; background: var(--card-white); }
  .back-brand {
    position: absolute;
    left: 34px;
    top: 38px;
    font-family: "Archivo Black", sans-serif;
    color: var(--ink);
    font-size: 30px;
    line-height: 1;
  }
  .back-brand span {
    display: block;
    font-size: 11.5px;
    letter-spacing: 5.2px;
    margin-top: 7px;
  }
  .accent-line {
    position: absolute;
    left: 34px;
    right: 30px;
    top: 140px;
    height: 1.5px;
    background: var(--brand-green);
  }
  .person { position: absolute; left: 34px; top: 154px; }
  .person-name {
    color: var(--brand-green);
    font-weight: 600;
    font-size: 24px;
    line-height: 1.1;
  }
  .person-title {
    color: var(--ink-soft);
    font-size: 13px;
    margin-top: 2px;
  }
  .contact-list {
    list-style: none;
    margin-top: 14px;
    font-size: 12.5px;
    color: var(--ink);
  }
  .contact-list li {
    display: flex;
    align-items: center;
    gap: 9px;
    line-height: 20px;
  }
  .contact-list svg { width: 12px; height: 12px; fill: var(--brand-green); flex: none; }
  .address {
    position: absolute;
    right: 30px;
    top: 220px;
    text-align: right;
    font-size: 12px;
    line-height: 17px;
    color: var(--ink);
  }
  .corner-bar {
    position: absolute;
    right: 0;
    bottom: 0;
    width: 190px;
    height: 14px;
    background: var(--brand-green);
  }
</style>
</head>
<body>

  <section class="card card-front" aria-label="Card front">
    <svg class="front-curve" viewBox="0 0 560 320" preserveAspectRatio="none" aria-hidden="true">
      <path d="M0 320 L0 300 C140 225 330 190 560 200 L560 215 C340 212 160 250 40 320 Z" fill="#ffffff"/>
    </svg>
    <div class="front-brand">
      <div class="brand-square"></div>
      <p class="brand-name">RIDGELINE<span>DESIGN + BUILD</span></p>
    </div>
  </section>

  <section class="card card-back" aria-label="Card back">
    <p class="back-brand">RIDGELINE<span>DESIGN + BUILD</span></p>
    <div class="accent-line"></div>
    <div class="person">
      <p class="person-name">Daniel Carter</p>
      <p class="person-title">Head contractor</p>
      <ul class="contact-list">
        <li>
          <svg viewBox="0 0 24 24"><path d="M6.6 10.8a15 15 0 0 0 6.6 6.6l2.2-2.2a1 1 0 0 1 1-.25 11 11 0 0 0 3.6.6 1 1 0 0 1 1 1V20a1 1 0 0 1-1 1A17 17 0 0 1 3 4a1 1 0 0 1 1-1h3.5a1 1 0 0 1 1 1 11 11 0 0 0 .6 3.6 1 1 0 0 1-.25 1z"/></svg>
          555.210.4400
        </li>
        <li>
          <svg viewBox="0 0 24 24"><path d="M7 1h10a2 2 0 0 1 2 2v18a2 2 0 0 1-2 2H7a2 2 0 0 1-2-2V3a2 2 0 0 1 2-2zm0 3v14h10V4zm5 15.5a1.2 1.2 0 1 0 0 2.4 1.2 1.2 0 0 0 0-2.4z"/></svg>
          555-210-4401
        </li>
        <li>
          <svg viewBox="0 0 24 24"><path d="M2 5h20v14H2zm2 2v.5l8 5 8-5V7zm0 2.8V17h16V9.8l-8 5z"/></svg>
          info@ridgeline-db.com
        </li>
        <li>
          <svg viewBox="0 0 24 24"><path d="M12 2a10 10 0 1 0 0 20 10 10 0 0 0 0-20zm6.9 9h-3a15 15 0 0 0-1.3-5.6A8 8 0 0 1 18.9 11zM12 4.1c.9 1.2 1.8 3.6 1.9 6.9h-3.8c.1-3.3 1-5.7 1.9-6.9zM9.4 5.4A15 15 0 0 0 8.1 11h-3a8 8 0 0 1 4.3-5.6zM5.1 13h3a15 15 0 0 0 1.3 5.6A8 8 0 0 1 5.1 13zm6.9 6.9c-.9-1.2-1.8-3.6-1.9-6.9h3.8c-.1 3.3-1 5.7-1.9 6.9zm2.6-1.3a15 15 0 0 0 1.3-5.6h3a8 8 0 0 1-4.3 5.6z"/></svg>
          www.ridgeline-db.com
        </li>
      </ul>
    </div>
    <p class="address">1420 Stonecrest Rd.<br>Cedar Hollow, GA 30512</p>
    <div class="corner-bar"></div>
  </section>

</body>
</html>
```